Law Offices business card

Hi there, I'll need business card for the Law Offices of Colin Matheny. The information must convey his strategic approach and quick resolution to complex business litigation needs. Please emphasize Civil Litigation, Corporate Law, Business Governance and Real Estate Law. Colin has over 25 years of experience in these fields.The card should be modern and edgy and the message should be clear. Please consult his current website for ideas.

```html
<!DOCTYPE html>
<html lang="en">
<head>
<meta charset="utf-8">
<title>Law Offices of Colin Matheny – Business Card</title>
<link href="https://fonts.googleapis.com/css2?family=Tinos:wght@400;700&family=Arimo:wght@400&display=swap" rel="stylesheet">
<style>
  :root {
    --page: #e9e7e3;
    --card: #fbfbfb;
    --ink: #1c1c1c;
    --muted: #555;
    --band-dark: #0b0b0b;
    --band-grey-1: #5c5c5c;
    --band-grey-2: #9a9a9a;
    --contact: #e8e8e8;
    --art-1: #ecebe8;
    --art-2: #d9d4cb;
  }
  * { box-sizing: border-box; margin: 0; padding: 0; }
  html, body { width: 1200px; height: 902px; overflow: hidden; }
  body { background: var(--page); position: relative; }

  .card {
    position: absolute;
    top: 296px;
    width: 540px;
    height: 310px;
    background: var(--card);
    box-shadow: 0 6px 18px rgba(0,0,0,.18);
    overflow: hidden;
  }
  .card--back { left: 45px; }
  .card--front { left: 615px; }

  /* Back side */
  .back-art {
    position: absolute;
    right: 20px;
    top: 18px;
    width: 190px;
    height: 160px;
    border-radius: 6px;
    background: linear-gradient(135deg, var(--art-1), var(--art-2));
    opacity: .7;
  }
  .services-title {
    position: absolute;
    left: 32px;
    top: 44px;
    font-family: "Tinos", serif;
    font-weight: 700;
    font-size: 40px;
    color: var(--ink);
  }
  .services-list {
    position: absolute;
    left: 58px;
    top: 108px;
    list-style: none;
  }
  .services-list li {
    display: flex;
    align-items: center;
    gap: 12px;
    font-family: "Arimo", sans-serif;
    font-size: 21px;
    color: var(--muted);
    line-height: 36px;
  }
  .services-list svg { width: 20px; height: 18px; flex: none; }
  .experience {
    position: absolute;
    left: 58px;
    top: 262px;
    font-family: "Arimo", sans-serif;
    font-size: 16px;
    color: var(--muted);
  }

  /* Front side */
  .front-top {
    position: absolute;
    inset: 0 0 auto 0;
    height: 152px;
    text-align: center;
  }
  .attorney-name {
    position: absolute;
    left: 0; right: 0;
    top: 22px;
    padding-left: 90px;
    font-family: "Tinos", serif;
    font-weight: 700;
    font-size: 36px;
    color: var(--ink);
  }
  .attorney-role {
    position: absolute;
    left: 0; right: 0;
    top: 66px;
    padding-left: 130px;
    font-family: "Arimo", sans-serif;
    font-size: 20px;
    color: var(--ink);
  }
  .firm-name {
    position: absolute;
    left: 28px;
    top: 104px;
    font-family: "Tinos", serif;
    font-size: 29px;
    color: var(--ink);
    white-space: nowrap;
  }
  .band-grey {
    position: absolute;
    left: 0; right: 0;
    top: 152px;
    height: 12px;
    background: linear-gradient(180deg, var(--band-grey-1), var(--band-grey-2));
  }
  .front-bottom {
    position: absolute;
    left: 0; right: 0;
    top: 164px;
    bottom: 0;
    background: var(--band-dark);
    padding-top: 14px;
    text-align: center;
  }
  .contact-line {
    font-family: "Arimo", sans-serif;
    font-size: 16px;
    line-height: 23px;
    color: var(--contact);
  }
</style>
</head>
<body>

  <section class="card card--back" aria-label="Card back: services">
    <div class="back-art" role="img" aria-label="Faint illustration of a graduation cap resting on law books"></div>
    <h2 class="services-title">Services :</h2>
    <ul class="services-list">
      <li><svg viewBox="0 0 20 18" aria-hidden="true"><g fill="none" stroke="#666" stroke-width="1.4"><line x1="10" y1="1" x2="10" y2="16"/><line x1="3" y1="4" x2="17" y2="4"/><line x1="6" y1="16.5" x2="14" y2="16.5"/><path d="M1 10 L3 4 L5 10 Z"/><path d="M15 10 L17 4 L19 10 Z"/></g></svg>Civil Litigation</li>
      <li><svg viewBox="0 0 20 18" aria-hidden="true"><g fill="none" stroke="#666" stroke-width="1.4"><line x1="10" y1="1" x2="10" y2="16"/><line x1="3" y1="4" x2="17" y2="4"/><line x1="6" y1="16.5" x2="14" y2="16.5"/><path d="M1 10 L3 4 L5 10 Z"/><path d="M15 10 L17 4 L19 10 Z"/></g></svg>Corporate Law</li>
      <li><svg viewBox="0 0 20 18" aria-hidden="true"><g fill="none" stroke="#666" stroke-width="1.4"><line x1="10" y1="1" x2="10" y2="16"/><line x1="3" y1="4" x2="17" y2="4"/><line x1="6" y1="16.5" x2="14" y2="16.5"/><path d="M1 10 L3 4 L5 10 Z"/><path d="M15 10 L17 4 L19 10 Z"/></g></svg>Business Governance</li>
      <li><svg viewBox="0 0 20 18" aria-hidden="true"><g fill="none" stroke="#666" stroke-width="1.4"><line x1="10" y1="1" x2="10" y2="16"/><line x1="3" y1="4" x2="17" y2="4"/><line x1="6" y1="16.5" x2="14" y2="16.5"/><path d="M1 10 L3 4 L5 10 Z"/><path d="M15 10 L17 4 L19 10 Z"/></g></svg>Real Estate Law</li>
    </ul>
    <p class="experience">Over 25 years of experience</p>
  </section>

  <section class="card card--front" aria-label="Card front: contact details">
    <div class="front-top">
      <h1 class="attorney-name">Colin Matheny</h1>
      <p class="attorney-role">Attorney</p>
      <p class="firm-name">Law Offices of Colin Matheny, P.A.</p>
    </div>
    <div class="band-grey"></div>
    <div class="front-bottom">
      <p class="contact-line">555-310-4827</p>
      <p class="contact-line">555-310-9264</p>
      <p class="contact-line">colin@mathenylaw.com</p>
      <p class="contact-line">www.mathenylaw.com</p>
      <p class="contact-line">118B Harbor Lane, Coral Bay, Florida 33012</p>
    </div>
  </section>

</body>
</html>
```